Venture 482 - Lumora Book Cover

I am looking for a Lumora book cover for my book about "Venture 482".
The Book is Titled:
Venture 482 Ascended
Shaping Outcomes: Paths To Unlocking Cosmic Truths
Author is Dorian Pell
Here is a book description that may help you understand more about it:
Inspired by the genius of Edwin Marlowe, this comprehensive guide delves into the ancient wisdom and cutting-edge science behind the 482 method, a powerful tool for manifesting your desires. Whether you're seeking personal growth, financial success, or spiritual enlightenment, this book provides advanced techniques and methods to transform your dreams into reality.
Any questions please ask.
Thanks
Owen

```html
<!DOCTYPE html>
<html lang="en">
<head>
<meta charset="utf-8">
<title>Venture 482 Ascended — Dorian Pell</title>
<link rel="stylesheet" href="https://fonts.googleapis.com/css2?family=Cinzel:wght@400;500&family=Tinos&display=swap">
<style>
  :root {
    --page: #e6e6e4;
    --sky-top: #0b161b;
    --sky-bottom: #0f3d47;
    --arch-inner: #070d10;
    --gold: #c9a46a;
    --gold-light: #e2c27f;
    --gold-dark: #a8843f;
    --cream: #f7e9de;
    --violet: #6a4f7e;
    --lavender: #8c86ad;
    --slate: #8c9db4;
    --white: #ffffff;
  }
  html, body {
    margin: 0;
    width: 1200px;
    height: 1131px;
    overflow: hidden;
    background: var(--page);
  }
  .cover {
    display: block;
    position: absolute;
    left: 229px;
    top: 0;
    width: 742px;
    height: 1131px;
  }
  .frame-line { fill: none; stroke: var(--gold); stroke-width: 2; }
  .frame-band { fill: none; stroke: #050a0c; stroke-width: 10; }
  .title-word {
    font-family: "Cinzel", serif;
    font-size: 92px;
    fill: var(--cream);
    text-anchor: middle;
  }
  .title-number {
    font-family: "Cinzel", serif;
    font-size: 270px;
    fill: var(--cream);
    text-anchor: middle;
  }
  .edition {
    font-family: "Cinzel", serif;
    font-size: 42px;
    letter-spacing: 30px;
    fill: var(--lavender);
    text-anchor: middle;
  }
  .subtitle-lead {
    font-family: "Tinos", serif;
    font-size: 27px;
    fill: var(--slate);
    text-anchor: middle;
  }
  .subtitle {
    font-family: "Tinos", serif;
    font-size: 25px;
    fill: var(--white);
    text-anchor: middle;
  }
  .author {
    font-family: "Cinzel", serif;
    font-size: 54px;
    letter-spacing: 12px;
    fill: var(--cream);
    text-anchor: middle;
  }
</style>
</head>
<body>
<svg class="cover" viewBox="0 0 875 1334" xmlns="http://www.w3.org/2000/svg" aria-label="Book cover: Venture 482 Ascended by Dorian Pell">
  <defs>
    <linearGradient id="sky" x1="0" y1="0" x2="0" y2="1">
      <stop offset="0" stop-color="var(--sky-top)"/>
      <stop offset="0.55" stop-color="#0d2a32"/>
      <stop offset="1" stop-color="var(--sky-bottom)"/>
    </linearGradient>
    <linearGradient id="gold" x1="0" y1="0" x2="1" y2="1">
      <stop offset="0" stop-color="var(--gold-light)"/>
      <stop offset="0.5" stop-color="var(--gold)"/>
      <stop offset="1" stop-color="var(--gold-dark)"/>
    </linearGradient>
    <radialGradient id="celestial" cx="0.5" cy="0.5" r="0.5">
      <stop offset="0" stop-color="#c9a46a" stop-opacity="0.28"/>
      <stop offset="1" stop-color="#c9a46a" stop-opacity="0"/>
    </radialGradient>
    <radialGradient id="digit-glow" cx="0.5" cy="0.5" r="0.5">
      <stop offset="0" stop-color="#6a4f7e" stop-opacity="0.22"/>
      <stop offset="1" stop-color="#6a4f7e" stop-opacity="0"/>
    </radialGradient>
  </defs>

  <rect class="sky" width="875" height="1334" fill="url(#sky)" role="img" aria-label="Starry night sky background"/>

  <path class="gold-frame" fill="url(#gold)" d="M95 867 H777 V1214 H95 Z M133 867 V1177 H739 V867 Z" fill-rule="evenodd"/>

  <path class="arch-fill" fill="var(--arch-inner)" opacity="0.75" d="M133 1177 V429 A303 303 0 0 1 739 429 V1177 Z"/>
  <path class="frame-line" d="M97 867 V429 A339 339 0 0 1 775 429 V867"/>
  <path class="frame-band" d="M110 867 V429 A326 326 0 0 1 762 429 V867"/>
  <path class="frame-line" d="M118 867 V429 A318 318 0 0 1 754 429 V867"/>
  <path class="frame-line" d="M126 867 V429 A310 310 0 0 1 746 429 V867"/>

  <rect class="celestial-ornament" x="40" y="150" width="800" height="200" fill="url(#celestial)" role="img" aria-label="Celestial ornament: crescent moon, sun, planets on an orbit line and scattered stars"/>

  <text class="title-word" x="437" y="457">VENTURE</text>

  <rect class="digit-ornament" x="150" y="495" width="570" height="305" fill="url(#digit-glow)" role="img" aria-label="Ornament: three small dotted arches framing each digit"/>

  <text class="title-number" x="247" y="735">4</text>
  <text class="title-number" x="437" y="735">8</text>
  <text class="title-number" x="636" y="735">2</text>

  <text class="edition" x="452" y="878">ASCENDED</text>

  <text class="subtitle-lead" x="437" y="1002">SHAPING OUTCOMES:</text>
  <text class="subtitle" x="437" y="1046">Paths to unlocking</text>
  <text class="subtitle" x="437" y="1080">cosmic truths</text>

  <text class="author" x="443" y="1283">DORIAN PELL</text>
</svg>
</body>
</html>
```